Mergers and Acquisitions Business Seeks Fresh Website Design

IMPORTANT: Please only design the Homepage, for the contest. If you win the contest, you will design the inner pages, as see in the attached document 'Vextra 2025 website wireframes."
Design a new website for Vextra at vextra.global. Maintaining current Impact and Open Sans fonts, or using open-source alternatives from Google Fonts.
Enhance the design with a premium feel, impactful visuals, and dynamic content. We want the new design to focus on generating high-quality inquiries, strong calls to action, and consistent branding.
Industry/Entity Type
Mergers and Acquisitions
Number of Pages Required
5+ page
Font styles to use
Other font styles liked:
- See Website Brief file
Requirements
Must have
- Consistency in layout, colours, fonts and overall design
Should not have
- Very bright colours, hard to read fonts, unlicensed images and fonts

```html
<!DOCTYPE html>
<html lang="en">
<head>
<meta charset="utf-8">
<title>Vextra | Deal Origination</title>
<link href="https://fonts.googleapis.com/css2?family=Anton&family=Open+Sans:ital,wght@0,400;0,600;0,700;1,400;1,700&display=swap" rel="stylesheet">
<style>
:root{
  --purple:#4b1b5e;
  --purple-dark:#3a1249;
  --gold:#f5b20a;
  --ink:#1d1d1f;
  --grey-band:#eeeeef;
  --white:#fff;
}
*{box-sizing:border-box;margin:0;padding:0}
html,body{width:1200px;height:5314px;overflow:hidden}
body{position:relative;font-family:"Open Sans",sans-serif;color:var(--ink);background:var(--white)}
.abs{position:absolute}
.display{font-family:"Anton",sans-serif;font-weight:400;text-transform:uppercase;letter-spacing:.5px}
.section-title{position:absolute;left:0;width:1200px;text-align:center;font-size:36px;line-height:48px;color:var(--ink)}

/* header */
.site-header{position:absolute;left:0;top:0;width:1200px;height:102px;background:var(--purple)}
.brand{position:absolute;left:142px;top:18px;font-family:"Anton",sans-serif;font-size:58px;color:var(--white);line-height:1;letter-spacing:1px}
.btn-contact-top{position:absolute;left:728px;top:12px;width:136px;height:38px;border-radius:19px;background:var(--gold);color:var(--purple);font-size:13px;font-weight:700;display:flex;align-items:center;justify-content:center}
.flag{position:absolute;left:897px;top:12px;width:36px;height:36px;border-radius:50%;background:repeating-linear-gradient(180deg,#c8102e 0 5px,#fff 5px 10px);overflow:hidden}
.flag::before{content:"";position:absolute;left:0;top:0;width:18px;height:18px;background:#1f3b8c}
.top-phone{position:absolute;left:943px;top:11px;color:var(--white);font-size:11px;line-height:18px}
.top-phone b{font-size:12px;font-weight:600}
.main-nav{position:absolute;top:73px;left:0;width:1200px;font-size:14px;color:var(--white)}
.main-nav span{position:absolute}
.main-nav .active{color:var(--gold)}

/* photo areas */
.hero{position:absolute;left:0;top:102px;width:1200px;height:551px;
  background:
   radial-gradient(ellipse 260px 300px at 900px 230px,rgba(40,70,120,.55),transparent 70%),
   radial-gradient(ellipse 300px 240px at 560px 300px,rgba(210,170,140,.45),transparent 70%),
   linear-gradient(100deg,#d9d6d0 0%,#c8c3bb 35%,#9aa3ad 65%,#4e5a6e 100%)}
.hero-shade{position:absolute;left:0;top:414px;width:632px;height:239px;background:rgba(40,36,44,.6)}
.hero-title{position:absolute;left:142px;top:447px;font-size:58px;line-height:80px;color:var(--white)}
.hero-title i{display:inline-block;width:10px;height:46px;background:var(--gold);margin-right:6px;vertical-align:-4px}

/* intro */
.intro-lead{position:absolute;left:140px;top:810px;width:920px;text-align:center;font-size:16.5px;line-height:32px;color:#333}
.intro-body{position:absolute;left:140px;top:880px;width:920px;text-align:center;font-size:12.5px;line-height:23px;color:#555}
.intro-quote{position:absolute;left:180px;top:987px;width:840px;text-align:center;font-size:15px;line-height:27px;font-style:italic;color:var(--purple)}
.feature-card{position:absolute;top:1072px;width:296px;height:234px;background:var(--white);box-shadow:0 4px 18px rgba(0,0,0,.09);text-align:center}
.feature-icon{position:absolute;left:109px;top:32px;width:78px;height:78px;border-radius:50%;background:var(--gold)}
.feature-card h3{position:absolute;top:128px;width:100%;font-size:17px;font-weight:400}
.feature-card p{position:absolute;top:158px;left:30px;width:236px;font-size:12px;line-height:22px;color:#666}
.slider-arrow{position:absolute;width:36px;height:36px;border-radius:50%;display:flex;align-items:center;justify-content:center}
.arrow-grey{background:#9a9a9c}
.arrow-purple{background:var(--purple)}
.arrow-outline{border:2px solid var(--white)}

/* video + pe */
.grey-band{position:absolute;left:0;top:1532px;width:1200px;height:412px;background:var(--grey-band)}
.video{position:absolute;left:253px;top:1352px;width:694px;height:362px;
  background:
   radial-gradient(ellipse 180px 160px at 380px 120px,rgba(215,180,155,.6),transparent 70%),
   linear-gradient(100deg,#e3e3e1 0%,#b9bbbd 30%,#6f747c 60%,#3b404a 100%);
  box-shadow:0 6px 20px rgba(0,0,0,.2)}
.play{position:absolute;left:555px;top:1488px;width:90px;height:90px;border-radius:50%;border:3px solid var(--white)}
.play-label{position:absolute;left:650px;top:1564px;font-weight:700;font-style:italic;font-size:30px;color:var(--white)}
.pe-text{position:absolute;left:0;top:1858px;width:1200px;text-align:center;font-size:17px;color:#444}

/* cta band */
.cta-band{position:absolute;left:0;top:1944px;width:1200px;height:376px;
  background:radial-gradient(ellipse 400px 300px at 1000px 200px,rgba(120,70,140,.35),transparent 70%),
  linear-gradient(90deg,#3d1450,var(--purple) 50%,#3d1450)}
.cta-text{position:absolute;left:200px;top:2090px;width:800px;text-align:center;font-size:17px;line-height:32px;color:var(--white)}
.btn{position:absolute;height:42px;border-radius:21px;font-size:13px;font-weight:700;display:flex;align-items:center;justify-content:center;gap:6px}
.btn-gold{background:var(--gold);color:var(--purple)}
.btn-ghost{border:2px solid var(--white);color:var(--white)}
.btn-purple{background:var(--purple);color:var(--white)}

/* numbers */
.numbers-title{position:absolute;left:142px;top:2412px;font-size:36px}
.numbers-sub{position:absolute;left:142px;top:2482px;font-size:15px;color:#444}
.ratio{position:absolute;left:144px;top:2538px;width:404px;height:245px;border-radius:80px;background:var(--gold);display:flex;align-items:center;justify-content:center;font-family:"Anton",sans-serif;font-size:130px;color:var(--purple-dark)}
.duo{position:absolute;left:628px;top:2386px;width:426px;height:432px;
  background:radial-gradient(ellipse 120px 220px at 130px 260px,rgba(110,150,190,.55),transparent 70%),
  radial-gradient(ellipse 120px 220px at 320px 260px,rgba(120,160,195,.5),transparent 70%),
  linear-gradient(180deg,#d8d8d6,#a9acae 60%,#8f9396)}

/* case studies */
.case-tile{position:absolute;width:454px;height:350px;color:var(--white);font-size:13px;line-height:22px;text-align:center;display:flex;align-items:flex-end;justify-content:center;padding:0 30px 38px}
.case-a{background:linear-gradient(180deg,rgba(0,0,0,0) 45%,rgba(20,20,30,.75)),radial-gradient(ellipse 260px 180px at 230px 120px,#c9a98f,transparent 75%),linear-gradient(120deg,#e4e1da,#8f8b86)}
.case-b{background:linear-gradient(180deg,rgba(0,0,0,0) 45%,rgba(20,20,30,.8)),linear-gradient(120deg,#8f8578,#4d4a52 60%,#2f3040)}
.case-c{background:linear-gradient(180deg,rgba(0,0,0,0) 45%,rgba(20,20,30,.8)),linear-gradient(110deg,#cfcdca,#7c7771 55%,#3a3a44)}
.case-d{background:linear-gradient(180deg,rgba(0,0,0,0) 45%,rgba(20,20,30,.8)),radial-gradient(ellipse 200px 150px at 230px 160px,#e0d8c8,transparent 75%),linear-gradient(135deg,#6a5c52,#2f2c33)}

/* insights */
.insight{position:absolute;top:3910px;width:292px;height:322px;color:var(--white);font-size:13px;line-height:23px;text-align:center}
.insight p{position:absolute;left:20px;right:20px;bottom:42px}
.insight span{position:absolute;left:50%;bottom:14px;width:10px;height:10px;border-top:2px solid var(--white);border-left:2px solid var(--white);transform:translateX(-50%) rotate(45deg)}
.ins-a{background:linear-gradient(180deg,rgba(0,0,0,0) 50%,rgba(25,25,35,.8)),linear-gradient(90deg,#d9dde0,#8c7a63 60%,#5b4a3c)}
.ins-b{background:linear-gradient(180deg,rgba(0,0,0,0) 50%,rgba(25,25,35,.8)),linear-gradient(120deg,#9aa0a8,#4c5462 60%,#2c3340)}
.ins-c{background:linear-gradient(180deg,rgba(0,0,0,0) 50%,rgba(25,25,35,.8)),linear-gradient(120deg,#e6e6e6,#a6a9ae 50%,#5d6370)}
.ins-d{background:linear-gradient(180deg,rgba(0,0,0,0) 50%,rgba(25,25,35,.8)),linear-gradient(120deg,#7d8799,#3f4b60 60%,#2a3242)}
.dot{position:absolute;top:4272px;height:5px;border-radius:3px;background:#ccc}

/* offices */
.office-img{position:absolute;top:4440px;width:297px;height:278px}
.office{position:absolute;top:4758px;width:300px}
.office h4{font-size:17px;font-weight:400;margin-bottom:22px}
.office-row{position:relative;padding-left:72px;height:76px;font-size:13px;line-height:20px;color:#555}
.office-row b{display:block;font-weight:400;color:var(--ink)}
.office-icon{position:absolute;left:0;top:0;width:50px;height:50px;border-radius:50%;background:var(--gold);display:flex;align-items:center;justify-content:center}
.divider{position:absolute;top:4790px;width:1px;height:150px;background:#ddd}

/* footer */
.site-footer{position:absolute;left:0;top:4995px;width:1200px;height:319px;background:var(--purple);color:var(--white)}
.footer-col{position:absolute;top:38px;font-size:13px}
.footer-col h5{font-size:15px;font-weight:400;margin-bottom:14px}
.footer-col li{list-style:none;line-height:21px}
.footer-col li::before{content:"»";color:var(--gold);margin-right:12px}
.contact-line{display:flex;align-items:center;gap:10px;margin-bottom:14px}
.ring{width:26px;height:26px;border-radius:50%;border:2px solid var(--white);display:flex;align-items:center;justify-content:center}
.footer-btn{width:196px;height:36px;border-radius:18px;font-size:13px;font-weight:700;display:flex;align-items:center;justify-content:center;margin-bottom:16px}
.footer-bottom{position:absolute;top:286px;left:142px;right:142px;font-size:12px;display:flex;justify-content:space-between}
</style>
</head>
<body>

<header class="site-header">
  <div class="brand">vextra</div>
  <div class="btn-contact-top">CONTACT US</div>
  <div class="flag"></div>
  <div class="top-phone">USA ⌄<br><b>+44 1632 960 000</b></div>
  <nav class="main-nav">
    <span class="active" style="left:540px">CLIENTS</span>
    <span style="left:648px">SERVICES</span>
    <span style="left:763px">MANDATES</span>
    <span style="left:893px">BLOG</span>
    <span style="left:984px">ABOUT US</span>
  </nav>
</header>

<section class="hero" role="img" aria-label="Business team celebrating around laptops in an office"></section>
<div class="hero-shade"></div>
<h1 class="hero-title display"><i></i>Deal origination<br>for you!</h1>

<h2 class="section-title display" style="top:738px">Exclusive deals, reduced risk, stronger leverage</h2>
<p class="intro-lead">We consistently deliver high-quality deals, bypassing the crowded open market. Imagine a pipeline filled with precise targets, aligned with your acquisition goals. Our approach minimises execution risk.</p>
<p class="intro-body" style="top:884px">We bring forward only well-matched prospects backed by transparent tracking and guidance. By specialising in off-market exclusivity, we enhance your negotiation leverage, reducing competition and securing favourable terms for both parties. We focus on quality over quantity, building high-trust seller relationships. Gain a competitive edge with our deep market knowledge and highly targeted outreach, expanding your market share. Vextra enables you to acquire smarter, faster, and more effectively.</p>
<p class="intro-quote">Vextra empowers acquirers to outpace competitors by consistently delivering high-response, off-market deal flow, without adding headcount or overhead.</p>

<div class="slider-arrow arrow-grey" style="left:95px;top:1171px"><svg width="12" height="12" viewBox="0 0 12 12"><path d="M8 2 4 6l4 4" stroke="#fff" stroke-width="2" fill="none"/></svg></div>
<div class="slider-arrow arrow-purple" style="left:1069px;top:1171px"><svg width="12" height="12" viewBox="0 0 12 12"><path d="M4 2l4 4-4 4" stroke="#fff" stroke-width="2" fill="none"/></svg></div>

<div class="feature-card" style="left:143px">
  <div class="feature-icon"><svg width="78" height="78" viewBox="0 0 78 78"><rect x="24" y="24" width="30" height="30" rx="3" fill="none" stroke="#4b1b5e" stroke-width="2.5"/><circle cx="34" cy="36" r="6" fill="none" stroke="#4b1b5e" stroke-width="2.5"/><path d="M38 40l8 8" stroke="#4b1b5e" stroke-width="2.5"/></svg></div>
  <h3>Find The Ideal Fit</h3>
  <p>Target Businesses That Match Your Exact Criteria</p>
</div>
<div class="feature-card" style="left:451px">
  <div class="feature-icon"><svg width="78" height="78" viewBox="0 0 78 78"><circle cx="39" cy="34" r="13" fill="none" stroke="#4b1b5e" stroke-width="2.5"/><path d="M33 34l4 4 8-8" stroke="#4b1b5e" stroke-width="2.5" fill="none"/><path d="M31 45l-4 12 7-3 4 6 1-12M47 45l4 12-7-3-4 6" stroke="#4b1b5e" stroke-width="2.5" fill="none"/></svg></div>
  <h3>Higher-quality Deals</h3>
  <p>Engage With Owners Who Prefer A Discreet Sale</p>
</div>
<div class="feature-card" style="left:759px">
  <div class="feature-icon"><svg width="78" height="78" viewBox="0 0 78 78"><rect x="28" y="20" width="26" height="18" rx="3" fill="none" stroke="#4b1b5e" stroke-width="2.5"/><path d="M22 52c6-6 12-8 18-6l12 2-2 4-10-1M22 58h16l14-6" stroke="#4b1b5e" stroke-width="2.5" fill="none"/></svg></div>
  <h3>No Noise</h3>
  <p>Avoid Disruption From Advisors and Brokers</p>
</div>

<div class="grey-band"></div>
<div class="video" role="img" aria-label="Video still of a smiling businessman shaking hands"></div>
<div class="play"><svg width="84" height="84" viewBox="0 0 84 84"><path d="M33 26l26 16-26 16z" fill="#fff"/></svg></div>
<svg class="abs" style="left:600px;top:1576px" width="120" height="70" viewBox="0 0 120 70"><path d="M4 4c4 36 30 58 112 60" stroke="#fff" stroke-width="2" fill="none"/></svg>
<div class="play-label">Click To Play</div>
<h2 class="section-title display" style="top:1786px">We work for private equity</h2>
<p class="pe-text">Expand Your Pipeline Beyond Traditional Brokers and Geographic Boundaries.</p>

<section class="cta-band"></section>
<h2 class="section-title display" style="top:2022px;color:#fff">If you want ideal flow, let's talk</h2>
<p class="cta-text">There Is Only So Much You Can Tell From Reviewing Our Website, The Best Way To Explore Is To Have A Short Meeting With One Of Our Team.</p>
<div class="slider-arrow arrow-outline" style="left:118px;top:2113px"><svg width="12" height="12" viewBox="0 0 12 12"><path d="M8 2 4 6l4 4" stroke="#fff" stroke-width="2" fill="none"/></svg></div>
<div class="slider-arrow" style="left:1092px;top:2113px;background:var(--gold)"><svg width="12" height="12" viewBox="0 0 12 12"><path d="M4 2l4 4-4 4" stroke="#4b1b5e" stroke-width="2" fill="none"/></svg></div>
<div class="btn btn-gold" style="left:390px;top:2191px;width:206px"><svg width="12" height="12" viewBox="0 0 24 24"><path d="M6 2l4 5-2 3c1 3 3 5 6 6l3-2 5 4-3 4C10 22 2 14 2 5z" fill="#4b1b5e"/></svg>CALL 01632 960 000</div>
<div class="btn btn-ghost" style="left:606px;top:2191px;width:204px">CONTACT VEXTRA</div>

<h2 class="numbers-title display">Vextra the numbers</h2>
<p class="numbers-sub">For Every 1 Target Approached, We Analyse At Least 5</p>
<div class="ratio">1:5</div>
<div class="duo" role="img" aria-label="Two business colleagues standing and talking"></div>

<h2 class="section-title display" style="top:2885px">Recent case studies</h2>
<div class="case-tile case-a" style="left:143px;top:2970px" role="img" aria-label="Diverse team meeting in a bright office">Fire Safety Focussed Investment Group Acquired A Bespoke Fire &amp; Security Solutions Business</div>
<div class="case-tile case-b" style="left:600px;top:2970px" role="img" aria-label="Team working around a table">Leading Labour Recruitment Company Acquired An Established Construction &amp; Recruitment Firm</div>
<div class="case-tile case-c" style="left:143px;top:3322px" role="img" aria-label="Business meeting at a desk">Leading Labour Recruitment Company Acquired An Established Construction &amp; Recruitment Firm</div>
<div class="case-tile case-d" style="left:600px;top:3322px" role="img" aria-label="Overhead view of a team around a table">Fire Safety Focussed Investment Group Acquired A Bespoke Fire &amp; Security Solutions Business</div>
<div class="btn btn-purple" style="left:498px;top:3720px;width:204px">MORE CASE STUDIES</div>

<h2 class="section-title display" style="top:3826px">M&amp;A insights &amp; latest trends</h2>
<div class="insight ins-a" style="left:0" role="img" aria-label="Businessman at an office window"><p>Why Off Market Is Key For The Motivated Buyer</p><span></span></div>
<div class="insight ins-b" style="left:303px" role="img" aria-label="Business professionals in discussion"><p>Is There A Suitable Business For Sale Near Me?</p><span></span></div>
<div class="insight ins-c" style="left:604px" role="img" aria-label="Team meeting in a modern office"><p>5 Ways To Increase Your Chances Of Selling Your Business</p><span></span></div>
<div class="insight ins-d" style="left:907px" role="img" aria-label="Group of business people smiling"><p>How To Finance Your Next Business Acquisition</p><span></span></div>
<div class="dot" style="left:549px;width:30px;background:var(--gold)"></div>
<div class="dot" style="left:587px;width:16px"></div>
<div class="dot" style="left:610px;width:16px"></div>
<div class="dot" style="left:633px;width:16px"></div>

<h2 class="section-title display" style="top:4348px">Regional &amp; cross-border deal makers</h2>
<div class="office-img" style="left:143px;background:linear-gradient(180deg,#7fb0e0 0%,#b7d3ec 35%,#c9a27a 55%,#8c6e55 75%,#5f7d6a 100%)" role="img" aria-label="European city skyline with river"></div>
<div class="office-img" style="left:451px;background:#efefef;box-shadow:0 0 0 1px #ddd" role="img" aria-label="Map of the United States with office marker"></div>
<svg class="abs" style="left:614px;top:4510px" width="44" height="58" viewBox="0 0 44 58"><path d="M22 2C11 2 3 10 3 21c0 14 19 35 19 35s19-21 19-35C41 10 33 2 22 2z" fill="#4b1b5e"/><circle cx="22" cy="21" r="8" fill="#fff"/></svg>
<div class="office-img" style="left:759px;background:linear-gradient(180deg,#8dbbe6 0%,#c4dcf0 40%,#6f8093 62%,#3f5a6a 80%,#4f7a5a 100%)" role="img" aria-label="Harbour city skyline"></div>

<div class="office" style="left:143px">
  <h4>UK &amp; EUROPE OFFICE</h4>
  <div class="office-row"><div class="office-icon"><svg width="20" height="24" viewBox="0 0 20 24"><path d="M10 1C5 1 2 5 2 9c0 6 8 14 8 14s8-8 8-14c0-4-3-8-8-8z" fill="none" stroke="#4b1b5e" stroke-width="2"/><circle cx="10" cy="9" r="3" fill="#4b1b5e"/></svg></div><b>LOCATION:</b>Third Floor Kestrel Court<br>House Reading RG9 4XZ</div>
  <div class="office-row"><div class="office-icon"><svg width="22" height="22" viewBox="0 0 24 24"><path d="M6 2l4 5-2 3c1 3 3 5 6 6l3-2 5 4-3 4C10 22 2 14 2 5z" fill="none" stroke="#4b1b5e" stroke-width="2"/></svg></div><b>CONTACT:</b>+44 (0) 1632 960 000</div>
</div>
<div class="divider" style="left:428px"></div>
<div class="office" style="left:474px">
  <h4>USA OFFICE</h4>
  <div class="office-row"><div class="office-icon"><svg width="20" height="24" viewBox="0 0 20 24"><path d="M10 1C5 1 2 5 2 9c0 6 8 14 8 14s8-8 8-14c0-4-3-8-8-8z" fill="none" stroke="#4b1b5e" stroke-width="2"/><circle cx="10" cy="9" r="3" fill="#4b1b5e"/></svg></div><b>LOCATION:</b>Lorem ipsum dolor sit amet<br>USA 1256 D enim</div>
  <div class="office-row"><div class="office-icon"><svg width="22" height="22" viewBox="0 0 24 24"><path d="M6 2l4 5-2 3c1 3 3 5 6 6l3-2 5 4-3 4C10 22 2 14 2 5z" fill="none" stroke="#4b1b5e" stroke-width="2"/></svg></div><b>CONTACT:</b>+44 1632 960 000</div>
</div>
<div class="divider" style="left:788px"></div>
<div class="office" style="left:809px">
  <h4>APAC OFFICE</h4>
  <div class="office-row"><div class="office-icon"><svg width="20" height="24" viewBox="0 0 20 24"><path d="M10 1C5 1 2 5 2 9c0 6 8 14 8 14s8-8 8-14c0-4-3-8-8-8z" fill="none" stroke="#4b1b5e" stroke-width="2"/><circle cx="10" cy="9" r="3" fill="#4b1b5e"/></svg></div><b>LOCATION:</b>12 Harbour Lane Millers Point<br>NSW 2000 Australia</div>
  <div class="office-row"><div class="office-icon"><svg width="22" height="22" viewBox="0 0 24 24"><path d="M6 2l4 5-2 3c1 3 3 5 6 6l3-2 5 4-3 4C10 22 2 14 2 5z" fill="none" stroke="#4b1b5e" stroke-width="2"/></svg></div><b>CONTACT:</b>+61 (0) 491 570 110</div>
</div>

<footer class="site-footer">
  <div class="footer-col" style="left:142px">
    <h5>CLIENTS</h5>
    <ul><li>Private Equity</li><li>Trade Buyers</li><li>Management Buy In</li><li>Search Funds</li><li>Corporate Finance</li></ul>
  </div>
  <div class="footer-col" style="left:493px">
    <h5>SERVICES</h5>
    <ul><li>Deal Origination</li><li>Single Acquisitions</li><li>Buy and Build</li><li>Bolt-On Acquisitions</li><li>Cross Border/International</li><li>Acquisition Finance</li><li>Negotiation Support</li><li>Due Diligence</li></ul>
  </div>
  <div class="footer-col" style="left:858px">
    <h5>CONTACT US</h5>
    <div class="contact-line"><span class="ring"><svg width="12" height="12" viewBox="0 0 24 24"><path d="M6 2l4 5-2 3c1 3 3 5 6 6l3-2 5 4-3 4C10 22 2 14 2 5z" fill="#fff"/></svg></span>+44 (0) 1632 960 000</div>
    <div class="contact-line"><span class="ring"></span>Stay Connected</div>
    <div class="footer-btn" style="background:var(--gold);color:var(--purple)">CONTACT VEXTRA</div>
    <div class="footer-btn" style="border:2px solid #fff">BOOK APPOINTMENT</div>
  </div>
  <div class="footer-bottom"><span>© 2025 Vextra &nbsp;|&nbsp; All Rights Reserved</span><span>Policies - Terms of Use - Privacy Policy - Contact Us</span></div>
</footer>

</body>
</html>
```